Give Gold Kite an Online Presence!

Gold Kite Property Maintenance is an Australian Owned property maintenance company who needs a stand out online presence.

GK maintains many buildings and sites and wants to appeal to a corporate professional market with their brand new website. GK is essentially a handyman service offering all maintenance services to home owners, office managers, real estate agents and strata managers.

The Website:
We need a corporate website that appeals to our broader customer base (property owners, property managers, office managers) the copy is being written by a professional so use filler text for now.

Things that we want:
Home page that sets us apart and appeals to the corporate and residential market. The home page needs to not focus on either the residential or commercial market. The home page should focus on our logo and branding. We have a logo already and it is attached to the brief, please use it and try to consider the colour pallette that goes with it. Whilst we want the site to appear strong and manly it is important to remember that 95% of our customers are female so we need the site to be appealing to women. Women need to believe that we are strong, dependable and trustworthy.
We'd like a quote page and potentially also the ability to get a quote from the home page (please don't put it in if it ruins the overall feel of the home page)
An "about us" page
A contact us page
A blog that's built in (we don't want to link to an external blog)
(overall we'd expect to have 6 or 7 pages total)

The site will also need coding - we expect this to be done in a separate project but need you to consider a few things about the coding side of things.

It needs to be iPhone and iPad compatible.

We'd like you to suggest the best CMS that you would use or if you would suggest not using a CMS please let us know with your submissions.

Target Market(s)

Property owners, office managers and property managers who need maintenance on buildings (So all of them)

Industry/Entity Type

Property Maintenance

Requirements
Must have
• Our Logo
Home page
About Us
Residential
Commercial
Real Estate/Strata
Contact Us/Quote
Blog
Nice to have
• Quote form included in home page
Movement on the home page at least
Should not have
• other logos, too much colour
NO FLASH

```html
<!DOCTYPE html>
<html lang="en">
<head>
<meta charset="utf-8">
<title>Gold Kite Property Maintenance</title>
<link href="https://fonts.googleapis.com/css2?family=PT+Sans:wght@400;700&family=Ubuntu:wght@500;700&display=swap" rel="stylesheet">
<style>
:root{
  --orange:#f7941d;
  --orange-deep:#ff5a00;
  --orange-head:#ff9c12;
  --dark:#2b2b2b;
  --darker:#1e1e1e;
  --grey-bg:#ebebeb;
  --wood:#6b3519;
  --wood-dark:#4a220f;
  --text:#333;
  --white:#fff;
}
*{margin:0;padding:0;box-sizing:border-box}
html,body{width:962px;height:1200px;overflow:hidden}
body{font-family:"PT Sans",Arial,sans-serif;color:var(--text);background:var(--grey-bg)}
.canvas{position:relative;width:962px;height:1200px;overflow:hidden;background:var(--grey-bg)}
.abs{position:absolute}
.wood-band{left:0;top:233px;width:962px;height:322px;background:repeating-linear-gradient(90deg,var(--wood) 0 18px,#74391b 18px 30px,var(--wood-dark) 30px 33px,#6f3619 33px 52px)}
.white-band{left:0;top:1043px;width:962px;height:98px;background:var(--white)}
.top-links{right:140px;top:7px;font-size:11px;color:#222;z-index:5}
.top-links span{margin:0 5px}
.brand{left:168px;top:30px;width:75px;height:75px;background:var(--dark);display:flex;flex-direction:column;align-items:center;justify-content:center;gap:6px}
.brand-mark{width:14px;height:14px;background:var(--orange)}
.brand-name{font-family:"Ubuntu",sans-serif;font-weight:700;font-size:12px;color:var(--orange);text-align:center;line-height:1.1}
.brand-shadow{left:128px;top:108px;width:150px;height:8px;background:radial-gradient(ellipse at center,rgba(0,0,0,.25),transparent 70%)}
.tools-photo{left:605px;top:32px;width:322px;height:200px;border-radius:48% 42% 46% 50%/55% 50% 50% 45%;background:radial-gradient(ellipse at 45% 40%,#c98a45 0,#9a5f2c 35%,#5a3a22 62%,rgba(235,235,235,0) 74%);z-index:1}
.nav{left:149px;top:121px;width:662px;height:51px;background:linear-gradient(#333,var(--darker));border-radius:8px 8px 0 0;display:flex;padding-left:46px;z-index:2}
.nav a{color:var(--white);text-decoration:none;font-size:13px;line-height:50px;padding:0 11px;position:relative}
.nav a.active::after{content:"";position:absolute;left:7px;right:7px;bottom:-2px;height:6px;background:var(--orange)}
.hero{left:113px;top:172px;width:736px;height:265px;background:linear-gradient(90deg,var(--orange-deep),#ff7a00 45%,#ffa033 70%,#f2f2f2);overflow:hidden;box-shadow:0 3px 8px rgba(0,0,0,.4);z-index:2}
.hero-person{left:20px;top:24px;width:190px;height:241px;background:radial-gradient(ellipse at 50% 30%,#4a3a33 0,#2d2d2d 55%,rgba(40,40,40,.0) 75%)}
.hero-house{left:470px;top:0;width:266px;height:265px;background:radial-gradient(ellipse at 70% 35%,#f4f4f4 0,#d9d9d9 28%,rgba(230,120,30,.8) 55%,rgba(61,95,138,.9) 100%)}
.hero-title{left:195px;top:56px;font-family:"Ubuntu",sans-serif;font-weight:700;font-size:30px;line-height:33px}
.hero-title .l1{color:#333}
.hero-title .l2{color:var(--white)}
.hero-text{left:195px;top:140px;width:230px;font-size:10.5px;line-height:14px;color:var(--white);text-align:justify}
.btn{display:inline-block;background:linear-gradient(#555,#2d2d2d);color:var(--white);border-radius:4px;text-align:center;font-size:10px;text-decoration:none}
.hero-btn{left:304px;top:221px;width:96px;height:20px;line-height:20px;font-size:12px;font-weight:700}
.dots{left:758px;top:437px;width:91px;height:21px;background:#dcdcdc;border-radius:0 0 6px 14px;display:flex;gap:8px;align-items:center;justify-content:center}
.dots i{width:8px;height:8px;background:#9a9a9a}
.dots i.on{background:var(--orange)}
.search-tab{left:587px;top:482px;width:262px;height:44px;background:var(--white);clip-path:polygon(6% 0,100% 0,100% 100%,0 100%);border-radius:6px 6px 0 0}
.search{left:617px;top:491px;width:204px;height:26px;border:1px solid #ccc;border-radius:13px;background:var(--white);font-size:13px;color:#777;padding:4px 14px}
.search svg{position:absolute;right:8px;top:5px}
.panel{left:111px;top:525px;width:738px;height:518px;background:var(--white);box-shadow:0 0 14px rgba(0,0,0,.18)}
.pic{border:1px solid #d8d8d8;box-shadow:inset 0 0 10px rgba(0,0,0,.18)}
.welcome-photo{left:131px;top:552px;width:95px;height:124px;background:radial-gradient(ellipse at 55% 30%,#e8c9a8 0,#3a3f8a 40%,#e9eef4 70%),#e9eef4}
.welcome-title{left:234px;top:583px;font-size:19px;color:var(--orange);font-family:"Ubuntu",sans-serif;font-weight:500}
.welcome-text{left:234px;top:612px;width:278px;font-size:9px;line-height:13px;text-align:justify;color:#333}
.small-btn{width:66px;height:14px;line-height:14px}
.offer{left:585px;top:557px;width:205px;height:121px;border-radius:8px;background:linear-gradient(90deg,var(--dark) 50%,#b99c4a 75%,#6d85a6);overflow:hidden}
.offer-title{left:12px;top:28px;font-family:"Ubuntu",sans-serif;font-weight:500;font-size:23px;line-height:21px}
.offer-title .o{color:var(--orange)}
.offer-title .w{color:var(--white)}
.offer-sub{left:13px;top:82px;font-size:13px;line-height:16px;color:var(--white);font-weight:700}
.divider{left:230px;top:703px;width:510px;height:3px;background:radial-gradient(ellipse at center,#c8c8c8,transparent 75%)}
.col-head{top:742px;height:29px;background:var(--orange-head);color:var(--white);font-size:12.5px;font-weight:700;line-height:29px;padding-left:9px;box-shadow:0 1px 2px rgba(0,0,0,.2)}
.testimonials{left:136px;top:802px;width:199px;font-size:10px;line-height:12.3px;text-align:justify}
.testimonials p{margin-bottom:34px}
.testimonials .who{display:block;color:var(--orange);text-align:left}
.video{left:371px;width:215px;height:58px}
.thumb{position:absolute;left:0;top:0;width:73px;height:58px}
.video h4{position:absolute;left:83px;top:0;color:var(--orange);font-size:11px;font-weight:400}
.video p{position:absolute;left:83px;top:14px;width:132px;font-size:10.5px;line-height:13px;text-align:justify}
.photo{width:73px;height:58px}
.social{top:1074px;width:36px;height:36px;border-radius:50%;background:var(--orange-deep)}
.social-label{top:1113px;font-size:11px;color:#777;text-align:center;width:60px}
.call{left:525px;top:1079px;font-family:"Ubuntu",sans-serif;font-weight:700;font-size:25px;color:#444;display:flex;align-items:center;gap:4px}
.footer{left:0;top:1141px;width:962px;height:59px;background:var(--darker)}
.copy{left:144px;top:1162px;color:var(--white);font-size:11px}
.foot-links{right:113px;top:1159px;display:flex;gap:24px;font-size:11.5px;color:var(--white)}
</style>
</head>
<body>
<div class="canvas">
  <div class="abs wood-band"></div>
  <div class="abs white-band"></div>

  <div class="abs tools-photo" role="img" aria-label="Leather tool belt full of hand tools"></div>
  <div class="abs top-links">Help<span>|</span>FAQs</div>

  <div class="abs brand-shadow"></div>
  <div class="abs brand"><span class="brand-mark"></span><span class="brand-name">Gold Kite</span></div>

  <nav class="abs nav">
    <a class="active">Home</a><a>About Us</a><a>Residential</a><a>Commercial</a><a>Real Estate/Strata</a><a>Contact Us/Quote</a><a>Blog</a>
  </nav>

  <section class="abs hero">
    <div class="abs hero-person" role="img" aria-label="Smiling businesswoman with folded arms"></div>
    <div class="abs hero-house" role="img" aria-label="Tradesman in tool belt holding a model house"></div>
    <h1 class="abs hero-title"><span class="l1">BEST SERVICES</span><br><span class="l2">IN AUSTRALIA</span></h1>
    <p class="abs hero-text">A handyman is a person skilled at a wide range of repairs, typically around the home. These tasks include trade skills, repair work, maintenance work, both interior and exterior, and are sometimes described as "odd jobs", light fixture.</p>
    <a class="abs btn hero-btn">Read more</a>
  </section>
  <div class="abs dots"><i class="on"></i><i></i><i></i><i></i></div>

  <div class="abs search-tab"></div>
  <div class="abs search">Search
    <svg width="20" height="16" viewBox="0 0 20 16"><circle cx="7" cy="7" r="5" fill="none" stroke="#666" stroke-width="2"/><line x1="11" y1="10" x2="17" y2="15" stroke="#666" stroke-width="3"/></svg>
  </div>

  <main class="abs panel"></main>

  <div class="abs welcome-photo pic" role="img" aria-label="Handyman in hard hat beside a yellow ladder"></div>
  <h2 class="abs welcome-title">Welcome to our Website</h2>
  <p class="abs welcome-text">The term handyman increasingly describes a paid worker, but it also includes non-paid homeowners or do-it-yourselfers. Tasks range painting, drywall repair, remodeling, minor plumbing work, minor electrical work, household carpentry, sheetrock, crown moulding, and furniture</p>
  <a class="abs btn small-btn" style="left:445px;top:677px">Read more</a>

  <div class="abs offer" role="img" aria-label="Offer banner with worker wearing a tool belt">
    <div class="abs offer-title"><span class="o">Free</span><br><span class="w">Services</span></div>
    <div class="abs offer-sub">Valid for<br>another 10 days</div>
  </div>

  <div class="abs divider"></div>

  <h3 class="abs col-head" style="left:128px;width:210px">Customer Testimonials</h3>
  <h3 class="abs col-head" style="left:368px;width:219px">Videos</h3>
  <h3 class="abs col-head" style="left:617px;width:210px">Recent Project Photos</h3>

  <div class="abs testimonials">
    <p>I trust Gold Kite to take care of my needs. I've been using them for over 1 years and they are dependable and do fantastic work at a fair price. I highly recommend them.<span class="who">Carla Dunn, Australia</span></p>
    <p>It was indeed a pleasure to work with Gold Kite and specifically, the craftsman, Reid. He was not only professional and knowledgeable about the projects that needed to be completed but also extremely cooperative.<span class="who">Nina Hale, Sydney</span></p>
  </div>
  <a class="abs btn small-btn" style="left:267px;top:1027px">Read more</a>

  <div class="abs video" style="top:790px"><div class="thumb pic" role="img" aria-label="Worker fitting floorboards" style="background:radial-gradient(ellipse at 40% 40%,#cdd6e0,#8a5a34 75%)"></div><h4>Video 1</h4><p>The term handyman increasingly describes a paid worker,</p></div>
  <div class="abs video" style="top:869px"><div class="thumb pic" role="img" aria-label="Handyman repairing a house exterior" style="background:radial-gradient(ellipse at 70% 45%,#c7c2b8,#9a4a2a 75%)"></div><h4>Video 2</h4><p>The term handyman increasingly describes a paid worker,</p></div>
  <div class="abs video" style="top:952px"><div class="thumb pic" role="img" aria-label="Worker walking past a building" style="background:radial-gradient(ellipse at 50% 60%,#c9b07a,#5c88a8 75%)"></div><h4>Video 3</h4><p>The term handyman increasingly describes a paid worker,</p></div>
  <a class="abs btn small-btn" style="left:519px;top:1027px">View more</a>

  <div class="abs photo pic" role="img" aria-label="Renovated room interior" style="left:646px;top:797px;background:radial-gradient(ellipse at 60% 50%,#d8c3a0,#8c3a2a 80%)"></div>
  <div class="abs photo pic" role="img" aria-label="Worker painting a wall" style="left:730px;top:797px;background:radial-gradient(ellipse at 45% 55%,#2e3a55,#efe4d8 70%)"></div>
  <div class="abs photo pic" role="img" aria-label="Sawing timber on a bench" style="left:646px;top:869px;background:radial-gradient(ellipse at 50% 60%,#b5834a,#e9dcc2 75%)"></div>
  <div class="abs photo pic" role="img" aria-label="Builder working on a deck" style="left:730px;top:869px;background:radial-gradient(ellipse at 40% 50%,#3b5a8a,#b9c7cf 75%)"></div>
  <div class="abs photo pic" role="img" aria-label="Measuring with a tape" style="left:646px;top:942px;background:radial-gradient(ellipse at 50% 50%,#d6b24a,#7fa25a 75%)"></div>
  <div class="abs photo pic" role="img" aria-label="Workbench in a garage" style="left:730px;top:942px;background:radial-gradient(ellipse at 50% 60%,#6a5e50,#cfcac0 75%)"></div>
  <a class="abs btn small-btn" style="left:737px;top:1027px">View more</a>

  <div class="abs social" style="left:167px"></div>
  <div class="abs social-label" style="left:155px">Friends</div>
  <div class="abs social" style="left:233px"></div>
  <div class="abs social-label" style="left:221px">Chirp</div>

  <div class="abs call">
    <svg width="18" height="24" viewBox="0 0 18 24"><path d="M5 1 L9 6 L7 9 Q8 14 12 17 L15 15 L17 20 L13 23 Q2 18 1 5 Z" fill="#444"/></svg>
    Call to : 1-800-55-0192
  </div>

  <footer class="abs footer"></footer>
  <div class="abs copy">© Gold Kite 2012 / All Rights Reserved.</div>
  <div class="abs foot-links"><span>Home</span><span>About</span><span>Contact</span><span>Privacy Policy</span><span>Terms &amp; Conditions</span></div>
</div>
</body>
</html>
```